Harborview Optical -Window Poster (Optometrist)

We are an optometry practice and we need a poster for a new store promotion for our window highlighting we now also sell 2 pairs of glasses as a package deal. The size will be 1300mm width x 1900mm height

The artwork will be displayed as a fabric banner in our shop window. We have 7 other banners with different services our business provides. The words needs to standout for passers by and the cars stopped at the traffic lights out front of our business. We already have signs with our logos phone number etc. so we won't need them included in the poster.

It would need to include the following information.

Two pair packages now available*

*Conditions apply

The artwork will be displayed as a fabric banner in our shop window. We have 7 other banners with different services our business provides. The words needs to standout for passers by and the cars stopped at the traffic lights out front of our business. We already have signs with our logos phone number etc. so we won't need them included in the poster. Thank you for your work it's amazing Added Saturday, February 18, 2017

The artwork will be displayed as a fabric banner in our shop window. We have 7 other banners with different services our business provides. The words needs to standout for passers by and the cars stopped at the traffic lights out front of our business. We already have signs with our logos phone number etc. so we won't need them included in the poster. Added Saturday, February 18, 2017

Target Market(s)

Cars driving past and stopped at traffic lights outside our store.

Industry/Entity Type

Optician

Requirements
Must have
• Poster must say:
• Two pair packages now available*
• *Conditions apply

```html
<!DOCTYPE html>
<html lang="en">
<head>
<meta charset="utf-8">
<title>Harborview Optical – Two Pair Packages Window Poster</title>
<link rel="stylesheet" href="https://fonts.googleapis.com/css2?family=Anton&family=Lato:wght@400;900&family=Oswald:wght@600&display=swap">
<style>
  :root {
    --paper: #ffffff;
    --mist-top: #ececed;
    --mist-bottom: #e2e2e3;
    --brand-red: #c9232a;
    --brand-red-deep: #a91f25;
    --headline-red: #ed1c24;
    --ink: #0a0a0a;
    --silver: #9a9c9e;
    --silver-light: #c8c9cb;
    --white: #ffffff;
  }
  html, body {
    margin: 0;
    padding: 0;
    width: 962px;
    height: 1200px;
    overflow: hidden;
    background: var(--paper);
  }
  .poster {
    display: block;
    width: 962px;
    height: 1200px;
  }
  .tagline {
    font-family: "Lato", sans-serif;
    font-weight: 400;
    font-size: 50px;
    letter-spacing: 1px;
    fill: var(--ink);
  }
  .tagline-mark { font-weight: 900; }
  .headline {
    font-family: "Anton", sans-serif;
    fill: var(--ink);
  }
  .headline-two { font-size: 140px; }
  .headline-pair { font-size: 206px; }
  .headline-packages {
    font-size: 186px;
    fill: var(--headline-red);
  }
  .headline-shadow { fill: var(--ink); }
  .disclaimer {
    font-family: "Oswald", sans-serif;
    font-weight: 600;
    font-size: 48px;
    letter-spacing: 4px;
    fill: var(--white);
  }
</style>
</head>
<body>
<svg class="poster" viewBox="0 0 962 1200" xmlns="http://www.w3.org/2000/svg" role="img" aria-label="Two pair packages now available, conditions apply">
  <defs>
    <linearGradient id="mist" x1="0" y1="0" x2="0" y2="1">
      <stop offset="0" stop-color="var(--mist-top)"/>
      <stop offset="1" stop-color="var(--mist-bottom)"/>
    </linearGradient>
    <linearGradient id="base-red" x1="0" y1="0" x2="1" y2="0">
      <stop offset="0" stop-color="var(--brand-red)"/>
      <stop offset="1" stop-color="var(--brand-red-deep)"/>
    </linearGradient>
  </defs>

  <!-- background -->
  <rect class="paper" width="962" height="1200" fill="var(--paper)"/>

  <!-- upper grey field -->
  <path class="upper-field" fill="url(#mist)"
        d="M0 0 H962 V110 C930 50 840 40 760 80 C640 150 560 320 430 420 C300 520 120 520 0 476 Z"/>

  <!-- upper red swoosh -->
  <path class="upper-swoosh" fill="var(--brand-red)"
        d="M0 476 C120 520 300 520 430 420 C560 320 640 150 760 80 C840 40 930 50 962 110 L962 150 C930 90 850 72 785 110 C665 190 600 400 465 500 C335 595 150 600 0 586 Z"/>

  <!-- upper silver line -->
  <path class="upper-line" fill="none" stroke="var(--silver-light)" stroke-width="2"
        d="M0 622 C200 612 385 560 505 440 C625 315 700 155 800 112 C880 80 940 140 962 225"/>

  <!-- lower silver bands -->
  <path class="lower-line-light" fill="none" stroke="var(--silver-light)" stroke-width="2"
        d="M0 1075 C120 960 300 880 450 868 C590 858 660 925 770 920 C870 915 935 835 962 760"/>
  <path class="lower-line" fill="none" stroke="var(--silver)" stroke-width="7"
        d="M0 1112 C100 1005 280 920 435 905 C575 892 655 960 765 952 C865 945 932 870 962 815"/>

  <!-- lower red field -->
  <path class="lower-field" fill="url(#base-red)"
        d="M0 1143 C80 1040 250 960 420 930 C560 905 650 980 760 975 C860 970 930 900 962 856 L962 1200 L0 1200 Z"/>

  <!-- copy -->
  <text class="tagline" x="38" y="268">NOW AVAILABLE<tspan class="tagline-mark">*</tspan></text>

  <text class="headline headline-two" x="885" y="452" text-anchor="end">TWO</text>
  <text class="headline headline-pair" x="906" y="636" text-anchor="end">PAIR</text>

  <text class="headline headline-packages headline-shadow" x="917" y="832" text-anchor="end">PACKAGES</text>
  <text class="headline headline-packages" x="923" y="826" text-anchor="end">PACKAGES</text>

  <text class="disclaimer" x="899" y="1107" text-anchor="end">*CONDITIONS APPLY</text>
</svg>
</body>
</html>
```